New Fun, Positive, energised looking Business Card Needed for High Achiever Coach

I am looking for a two sided full colour business card. I am self employed and have recently re branded my 1-2-1 work re-vitalising high achievers. My target client base for these cards is therefore high achievers - usually aged 40 -55, they are often entrepreneurs, CEO or work in banking and finance and 2/3 are male. I work with them on 90 day or 6 month coaching programs to help them live their success in a healthier, more sustainable and fulfiiled way. They pay for this privately so though they are corporate types the cards need not look 'corporate'. I want to portray the idea of transformation, vitality and re-connecting.
You can get a feel for the look I like on my new website: morvenlisk.co.uk
I want to use this logo with strapline (Re-Vitalising High Achievers) (I purchased off Logoharbor) and font/ colours (the turquoise and green).
Details to include on the card:
www.morvenlisk.co.uk
+44 7915 302618
morven@morvenlisk.co.uk
skype: morvenlisk
I'd also like to include:
Do you struggle to switch off? Want to be healthier and feel fitter? Want closer relationships? More clarity over the direction you are headed? I can help you do these things using integrated mind-body techniques. Visit morvenlisk.co.uk TODAY to apply for a FREE Breakthrough session.
BUT if that is too much text for a card I am open to advice/ammendments.
Updates
Thanks for your design - I am considering them. PLease change the wording to :

```html
<!DOCTYPE html>
<html lang="en">
<head>
<meta charset="utf-8">
<title>Morven Lisk – Business Card</title>
<link rel="stylesheet" href="https://fonts.googleapis.com/css2?family=Open+Sans:wght@400;600;700&display=swap">
<style>
  :root {
    --stage: #e8e5e0;
    --card-black: #050505;
    --turquoise: #22a8d4;
    --leaf-green: #6cbf5a;
    --white: #ffffff;
    --soft-white: #e9e9e9;
    --divider: #8a8a8a;
  }
  * { box-sizing: border-box; margin: 0; padding: 0; }
  html, body {
    width: 1200px;
    height: 720px;
    overflow: hidden;
  }
  body {
    background: var(--stage);
    font-family: "Open Sans", Arial, sans-serif;
    display: flex;
    align-items: center;
    justify-content: center;
    gap: 40px;
  }
  .card {
    position: relative;
    width: 560px;
    height: 320px;
    background: var(--card-black);
    color: var(--white);
    overflow: hidden;
    box-shadow: 0 6px 18px rgba(0,0,0,0.18);
  }

  /* ---------- Front ---------- */
  .web-band {
    position: absolute;
    left: 0;
    right: 0;
    top: 42px;
    height: 38px;
    background: var(--turquoise);
    border-top: 2px solid var(--card-black);
    border-bottom: 2px solid var(--card-black);
    box-shadow: 0 -2px 0 var(--leaf-green), 0 2px 0 var(--leaf-green);
    display: flex;
    align-items: center;
    justify-content: center;
  }
  .web-band__url {
    font-size: 15px;
    font-weight: 600;
    letter-spacing: 0.28em;
    color: var(--white);
  }
  .brand {
    position: absolute;
    left: 34px;
    top: 170px;
    width: 170px;
    display: flex;
    align-items: center;
    gap: 8px;
  }
  .brand__dot {
    width: 12px;
    height: 12px;
    border-radius: 50%;
    background: var(--turquoise);
    flex: none;
  }
  .brand__name {
    font-size: 21px;
    font-weight: 700;
    color: var(--turquoise);
    white-space: nowrap;
  }
  .front-divider {
    position: absolute;
    left: 222px;
    top: 118px;
    width: 2px;
    height: 150px;
    background: linear-gradient(to bottom, transparent, var(--divider) 45%, var(--white) 55%, transparent);
  }
  .contact-list {
    position: absolute;
    left: 246px;
    top: 132px;
    list-style: none;
    display: flex;
    flex-direction: column;
    gap: 16px;
  }
  .contact-list__item {
    display: flex;
    align-items: center;
    gap: 8px;
    font-size: 14px;
    color: var(--soft-white);
  }
  .contact-list__icon {
    width: 13px;
    height: 13px;
    flex: none;
  }
  .contact-list__square {
    width: 11px;
    height: 11px;
    background: var(--turquoise);
    flex: none;
    margin: 0 1px;
  }

  /* ---------- Back ---------- */
  .pitch {
    position: absolute;
    inset: 0;
    display: flex;
    flex-direction: column;
    align-items: center;
    justify-content: center;
    text-align: center;
    gap: 14px;
    font-size: 17px;
    line-height: 1.3;
    color: var(--white);
  }
  .pitch strong { font-weight: 700; }
</style>
</head>
<body>

  <section class="card card--front" aria-label="Business card front">
    <div class="web-band">
      <span class="web-band__url">www.morvenlisk.co.uk</span>
    </div>

    <div class="brand">
      <span class="brand__dot"></span>
      <span class="brand__name">Morven Lisk</span>
    </div>

    <div class="front-divider"></div>

    <ul class="contact-list">
      <li class="contact-list__item">
        <svg class="contact-list__icon" viewBox="0 0 16 16" aria-hidden="true">
          <circle cx="8" cy="8" r="7" fill="none" stroke="#e9e9e9" stroke-width="1.4"/>
          <path d="M5.3 4.3l1.4-.2.8 1.9-.9.7c.4.9 1 1.6 1.9 2.1l.8-.8 1.9.9-.2 1.4c-2.9.2-5.9-2.9-5.7-6z" fill="#e9e9e9"/>
        </svg>
        +44 7915 302618
      </li>
      <li class="contact-list__item">
        <svg class="contact-list__icon" viewBox="0 0 16 16" aria-hidden="true">
          <rect x="1" y="3.5" width="14" height="9.5" rx="1" fill="#e9e9e9"/>
          <path d="M1.5 4l6.5 5 6.5-5" fill="none" stroke="#050505" stroke-width="1.3"/>
        </svg>
        morven@morvenlisk.co.uk
      </li>
      <li class="contact-list__item">
        <span class="contact-list__square"></span>
        morvenlisk
      </li>
    </ul>
  </section>

  <section class="card card--back" aria-label="Business card back">
    <div class="pitch">
      <p>Do you struggle to switch off?<br>
         Want to be healthier and feel fitter?<br>
         Want closer relationships?<br>
         More clarity over the direction you are headed?</p>
      <p>I can help you do these things using integrated<br>
         mind-body techniques.</p>
      <p>Visit <strong>morvenlisk.co.uk</strong> TODAY to apply for a<br>
         FREE Breakthrough session.</p>
    </div>
  </section>

</body>
</html>
```